Business card design for Virtual Assistance company

I need a business card designed for my virtual assistance company. We are a small company who services primarily C-level executive clients. The card needs to be double sided with the following contact information on the back:
Melissa Thornbury
Owner/CEO
info@rkpadvisory.net
www.rkpadvisory.net
555.302.9817

The front side should just have the company name incorporated: "RKP Advisory" and "virtual assistance"

The card should be simplistic, but eye catching and should speak to high level executives. Our primary focus areas consist of executive assistance and government contracting.

Target Market(s)

CEOs and executives

Contact Information for Business Card

see project description. phone, email, website.

Colors

Designer to choose only greyscale colors for use in the design.

```html
<!DOCTYPE html>
<html lang="en">
<head>
<meta charset="UTF-8">
<title>RKP Advisory — Business Card</title>
<link rel="stylesheet" href="https://fonts.googleapis.com/css2?family=Playfair+Display:wght@400;500&family=Montserrat:wght@400;700&display=swap">
<style>
  :root {
    --bg: #d9d7d3;
    --card-light: #ffffff;
    --card-dark: #1f1f1f;
    --ink: #1a1a1a;
    --ink-soft: #3a3a3a;
    --paper: #f4f4f2;
    --shadow: rgba(0, 0, 0, 0.28);
  }
  * { box-sizing: border-box; margin: 0; padding: 0; }
  html, body {
    width: 900px;
    height: 1200px;
    overflow: hidden;
  }
  body {
    background: var(--bg);
    position: relative;
    font-family: "Montserrat", sans-serif;
    color: var(--ink);
  }
  .card {
    position: absolute;
    left: 102px;
    width: 696px;
    height: 405px;
    border-radius: 26px;
    box-shadow: 0 10px 24px var(--shadow);
    overflow: hidden;
  }
  .card--front { top: 168px; background: var(--card-light); }
  .card--back { top: 636px; background: var(--card-dark); }

  .brand {
    position: absolute;
    left: 40px;
    top: 44px;
  }
  .brand__name {
    font-family: "Playfair Display", serif;
    font-weight: 400;
    font-size: 40px;
    line-height: 1;
    color: var(--ink);
  }
  .brand__tagline {
    font-family: "Playfair Display", serif;
    font-size: 15px;
    letter-spacing: 1.5px;
    text-transform: uppercase;
    margin-top: 12px;
    margin-left: 28px;
    color: var(--ink-soft);
  }
  .person {
    position: absolute;
    right: 40px;
    top: 42px;
    text-align: right;
  }
  .person__name {
    font-family: "Playfair Display", serif;
    font-weight: 500;
    font-size: 24px;
    color: var(--ink);
  }
  .person__title {
    font-size: 15px;
    margin-top: 4px;
    color: var(--ink-soft);
  }
  .wordmark {
    position: absolute;
    font-family: "Playfair Display", serif;
    font-weight: 400;
    line-height: 1;
    white-space: nowrap;
  }
  .card--front .wordmark {
    right: 40px;
    top: 190px;
    font-size: 58px;
    color: var(--ink);
  }
  .card--back .wordmark {
    left: 0;
    right: 0;
    top: 160px;
    text-align: center;
    font-size: 74px;
    color: var(--paper);
  }
  .contact {
    position: absolute;
    left: 40px;
    bottom: 42px;
    list-style: none;
  }
  .contact__item {
    display: flex;
    align-items: center;
    gap: 12px;
    font-size: 15px;
    line-height: 1;
    margin-top: 14px;
    color: var(--ink);
  }
  .contact__icon { width: 15px; height: 15px; flex: none; }
</style>
</head>
<body>
  <section class="card card--front" aria-label="Card front">
    <div class="brand">
      <div class="brand__name">RKP Advisory</div>
      <div class="brand__tagline">Virtual Assistance</div>
    </div>
    <div class="person">
      <div class="person__name">Melissa Thornbury</div>
      <div class="person__title">Owner/CEO</div>
    </div>
    <div class="wordmark">RKP Advisory</div>
    <ul class="contact">
      <li class="contact__item">
        <svg class="contact__icon" viewBox="0 0 24 24" aria-hidden="true"><path fill="#1a1a1a" d="M6.6 10.8a15.1 15.1 0 0 0 6.6 6.6l2.2-2.2c.3-.3.7-.4 1-.2 1.1.4 2.3.6 3.6.6.6 0 1 .4 1 1V20c0 .6-.4 1-1 1A17 17 0 0 1 3 4c0-.6.4-1 1-1h3.5c.6 0 1 .4 1 1 0 1.3.2 2.5.6 3.6.1.3 0 .7-.2 1z"/></svg>
        555.302.9817
      </li>
      <li class="contact__item">
        <svg class="contact__icon" viewBox="0 0 24 24" aria-hidden="true"><rect x="2" y="5" width="20" height="14" rx="2" fill="#1a1a1a"/><path d="M3 6l9 7 9-7" fill="none" stroke="#fff" stroke-width="1.8"/></svg>
        info@rkpadvisory.net
      </li>
      <li class="contact__item">
        <svg class="contact__icon" viewBox="0 0 24 24" aria-hidden="true"><circle cx="12" cy="12" r="10" fill="#1a1a1a"/><path d="M2 12h20M12 2c3 3 3 17 0 20M12 2c-3 3-3 17 0 20" fill="none" stroke="#fff" stroke-width="1.4"/></svg>
        www.rkpadvisory.net
      </li>
    </ul>
  </section>

  <section class="card card--back" aria-label="Card back">
    <div class="wordmark">RKP Advisory</div>
  </section>
</body>
</html>
```